Webdesign for a business that converts shops into apps. UPDATE BRIEF

We want a creative/professional design for our new business Vorbo.

Vorbo is a service that can deliver instant apps for quillora shops. So every shop owner can have its own app for selling to there customers.

We are open for your interpretation of the design. We think it could be intersting doing an onepage design for this. But thats not set in stones offcourse.

We need several section:
top section
some facts abt the service and maybe our company
price table
some customer review
functionalitys of the app (in a nice way shown)
Section showing screens of a demo shop.
footer with ccdetails, socialmedia, newsletter

I have been playing abit myself with a theme, but no development/designer experience. And we really need a very professional and custom look.

Ps. we are an ecommerce company so if we find any good designer here, we will have enough work for you.

Some competitors in this field;

http://shrt.example/k7Tq2Zw
http://shrt.example/p3Nx9Ld

Here is a design we like
http://brelunoweb.example/

Hoping for some great concepts!

Kind Regards and good luck!

Some screenshots which can be used for app demo;

UPDATE BRIEF

We would like to add a section for features of the app.
We would like to show a zelphone screen and all the most important features of the app and when clicking every feature the screen would change or the feature intened would be high lighted in some way.

The features and any content and info abt that can be used from
https://www.tovexa.example/features.html/

We need an how it works section aswell in the design, also that can be used content from here
https://www.tovexa.example/how-it-works/

Tovexa is our partner, so there work way and features are same as ours. We just want it in a different 'look and feel/design)

Reason: Getting very few good design at the moment. Same designers seem to be responding whith 5 designs at a time of low quality.

Target Market(s)

quillora webshop

Industry/Entity Type

Business

Number of Pages Required

1 page

Font styles to use
Sans Serif

Colors
0355a3
3176b5
85acd3
85cae6
33a6d7
0392cd
f59195
33b8a4

Requirements
Must have
• a creative and custom look, not a copied theme vibe.
Nice to have
• it would be nice if the entire design has a nice flow goinf through the site. The customers experience should be on point.
Should not have
• boring static experience

```html
<!DOCTYPE html>
<html lang="en">
<head>
<meta charset="utf-8">
<title>Vorbo – Instant apps for quillora shops</title>
<link rel="stylesheet" href="https://fonts.googleapis.com/css2?family=Roboto:wght@300;400;500;700&display=swap">
<style>
:root{
  --blue-deep:#0355a3;
  --blue:#3176b5;
  --blue-soft:#85acd3;
  --sky:#85cae6;
  --sky-mid:#33a6d7;
  --cyan:#0392cd;
  --coral:#f0545a;
  --pink:#f59195;
  --teal:#33b8a4;
  --ink:#1c1f2a;
  --grey:#6b6f78;
  --mist:#f4f5f7;
  --footer:#1f62ad;
  --white:#ffffff;
}
*{box-sizing:border-box;margin:0;padding:0}
html,body{width:1200px;height:3905px;overflow:hidden}
body{font-family:"Roboto",Arial,sans-serif;color:var(--ink);background:var(--white);position:relative}
section,footer,header{position:absolute;left:0;width:1200px;overflow:hidden}
.placeholder{position:absolute}
.btn{position:absolute;display:flex;align-items:center;justify-content:center;font-size:17px;font-weight:400;letter-spacing:.3px;text-decoration:none}
.btn-white{background:var(--white);color:var(--blue-deep)}
.btn-coral{background:var(--coral);color:var(--white)}
.section-title{position:absolute;left:0;width:1200px;text-align:center;font-weight:700;font-size:38px}
.slider-arrow{position:absolute;width:22px;height:40px}

/* hero */
.hero{top:0;height:672px;background:linear-gradient(135deg,#3b8fd0 0%,#2f7fc2 45%,#246fb5 100%)}
.hero-facets{position:absolute;inset:0}
.brand{position:absolute;left:100px;top:18px;font-size:70px;font-weight:500;color:var(--white);letter-spacing:-1px}
.nav{position:absolute;left:466px;top:52px;display:flex;gap:30px;align-items:center;font-size:13px;color:var(--white);letter-spacing:.3px}
.nav .signup{border:1px solid rgba(255,255,255,.8);padding:8px 12px}
.hero-title{position:absolute;left:100px;top:205px;width:620px;font-size:50px;line-height:56px;font-weight:700;color:var(--white)}
.hero-sub{position:absolute;left:100px;top:383px;width:600px;font-size:25px;line-height:30px;font-weight:300;color:var(--white)}

/* welcome */
.welcome{top:672px;height:518px;background:var(--white)}
.welcome-lead{position:absolute;left:140px;width:920px;top:95px;text-align:center;font-size:18px;line-height:30px;color:var(--grey);font-weight:300}
.fact{position:absolute;top:190px;width:300px;text-align:center}
.fact-badge{width:140px;height:140px;margin:0 auto;border-radius:50%;border:5px solid #e9eef4;display:flex;align-items:center;justify-content:center}
.fact-badge span{width:128px;height:128px;border-radius:50%;display:flex;align-items:center;justify-content:center}
.fact-value{font-size:42px;font-weight:500;color:var(--coral);margin-top:14px}
.fact-text{font-size:14px;line-height:21px;color:var(--grey);margin-top:4px;padding:0 18px}

/* pricing */
.pricing{top:1190px;height:468px;background:var(--mist)}
.pricing-lead{position:absolute;left:100px;top:112px;width:780px;font-size:26px;line-height:32px;font-weight:300;color:var(--ink);z-index:1}
.pricing-copy{position:absolute;left:100px;top:218px;width:740px;font-size:14px;line-height:21px;color:var(--grey);font-weight:300;z-index:1}
.pricing-device{left:700px;top:150px;width:500px;height:318px;background:linear-gradient(160deg,#ffffff 0%,#eef0f3 55%,#d9dde3 100%);clip-path:polygon(260px 0,500px 0,500px 318px,60px 318px)}

/* reviews */
.reviews{top:1658px;height:352px;background:linear-gradient(135deg,#3d85c6 0%,#2f75b8 55%,#2a6aae 100%);color:var(--white)}
.review-quote{position:absolute;left:210px;width:780px;top:128px;text-align:center;font-size:18px;font-weight:400}
.review-body{position:absolute;left:190px;width:820px;top:156px;text-align:center;font-size:13px;line-height:22px;font-weight:300}
.review-author{position:absolute;left:0;width:1200px;top:232px;display:flex;justify-content:center;align-items:center;gap:16px}
.avatar{width:62px;height:62px;border-radius:50%;background:linear-gradient(#d7dde4,#aeb8c3);border:3px solid var(--white)}
.author-name{font-size:17px;font-weight:300}

/* screens */
.screens{top:2010px;height:632px;background:var(--white)}
.device{position:absolute;top:120px;width:198px;height:410px;border-radius:30px;background:#f2f3f5;border:2px solid #d6d9de}
.device .speaker{position:absolute;left:74px;top:28px;width:50px;height:5px;border-radius:3px;background:#c7cbd1}
.device .screen{position:absolute;left:12px;top:58px;width:170px;height:296px;background:linear-gradient(#ffffff,#e9ecef)}
.device .home{position:absolute;left:79px;bottom:12px;width:38px;height:38px;border-radius:50%;border:2px solid #c7cbd1}
.dots{position:absolute;left:0;width:1200px;top:575px;display:flex;justify-content:center;gap:6px}
.dots i{width:12px;height:12px;border-radius:50%;border:2px solid var(--coral)}
.dots i.on{background:var(--coral)}

/* cta band */
.cta{top:2642px;height:435px}
.cta-title{position:absolute;left:0;width:1200px;top:146px;text-align:center;color:var(--white);font-size:38px;font-weight:700}

/* functions */
.functions{top:3077px;height:497px;background:var(--white)}
.functions-lead{position:absolute;left:100px;top:142px;width:540px;font-size:24px;line-height:29px;font-weight:300;color:var(--ink)}
.functions-copy{position:absolute;left:100px;width:540px;font-size:14px;line-height:21px;color:var(--grey);font-weight:300}

/* footer */
.site-footer{top:3574px;height:331px;background:linear-gradient(135deg,#2a71b8,#1c5da8);color:var(--white)}
.col-title{position:absolute;top:44px;font-size:15px;font-weight:500;letter-spacing:.5px}
.link-list{position:absolute;top:84px;list-style:none;font-size:14px;line-height:31px;font-weight:300}
.newsletter-note{position:absolute;left:776px;top:82px;font-size:14px;font-weight:300}
.email-field{position:absolute;left:776px;top:112px;width:218px;height:40px;background:var(--white);color:#b0b5bc;font-size:12px;padding:13px 14px;letter-spacing:.5px}
.subscribe{position:absolute;left:994px;top:112px;width:106px;height:40px;background:var(--coral);font-size:14px;font-weight:500;display:flex;align-items:center;justify-content:center}
.social{position:absolute;left:776px;top:172px;display:flex;gap:8px}
.social i{width:38px;height:38px;border-radius:50%;background:var(--white)}
.footer-rule{position:absolute;left:100px;top:266px;width:1000px;height:1px;background:rgba(255,255,255,.35)}
.copyright{position:absolute;left:100px;top:288px;font-size:12px;font-weight:300;opacity:.85}
</style>
</head>
<body>

<header class="hero">
  <svg class="hero-facets" width="1200" height="672" aria-hidden="true">
    <polygon points="0,0 420,0 0,380" fill="#ffffff" opacity=".04"/>
    <polygon points="420,0 900,0 640,420" fill="#ffffff" opacity=".05"/>
    <polygon points="0,380 640,420 300,672 0,672" fill="#000000" opacity=".04"/>
    <polygon points="900,0 1200,0 1200,500" fill="#000000" opacity=".05"/>
    <polygon points="640,420 1200,500 1200,672 300,672" fill="#ffffff" opacity=".03"/>
  </svg>
  <div class="brand">vorbo</div>
  <nav class="nav">
    <span>FEATURES</span><span>PRICING</span><span>SERVICES</span><span>SUPPORT</span><span>BLOG</span><span>LOG IN</span><span class="signup">SIGN UP</span>
  </nav>
  <svg class="slider-arrow" style="left:28px;top:320px" viewBox="0 0 22 40" aria-hidden="true"><polyline points="18,4 4,20 18,36" fill="none" stroke="#ffffff" stroke-opacity=".6" stroke-width="3"/></svg>
  <svg class="slider-arrow" style="right:28px;top:320px" viewBox="0 0 22 40" aria-hidden="true"><polyline points="4,4 18,20 4,36" fill="none" stroke="#ffffff" stroke-opacity=".6" stroke-width="3"/></svg>
  <h1 class="hero-title">Vorbo is a service that can deliver instant apps for quillora shops</h1>
  <p class="hero-sub">So every shop owner can have its own app for selling to there customers</p>
  <a class="btn btn-white" style="left:100px;top:470px;width:210px;height:55px">REQUEST A DEMO</a>
  <div class="placeholder" role="img" aria-label="Hand holding a smartphone showing the Vorbo app start screen" style="left:790px;top:165px;width:250px;height:507px;background:linear-gradient(180deg,#e9edf2 0%,#f3d6c4 70%,#e8bfa6 100%);border-radius:34px 34px 0 0"></div>
</header>

<section class="welcome">
  <h2 class="section-title" style="top:42px">Welcome to Vorbo</h2>
  <p class="welcome-lead">Vorbo is a service that can deliver instant apps for quillora shops. So every shop owner can have its own app for selling to there customers.</p>

  <div class="fact" style="left:100px">
    <div class="fact-badge"><span style="background:var(--blue)">
      <svg width="50" height="70" viewBox="0 0 50 70" aria-hidden="true"><rect x="2" y="2" width="46" height="66" rx="7" fill="#ffffff"/><rect x="7" y="10" width="36" height="46" fill="#3176b5"/><g fill="#ffffff"><rect x="11" y="14" width="8" height="8"/><rect x="21" y="14" width="8" height="8"/><rect x="31" y="14" width="8" height="8"/><rect x="11" y="25" width="8" height="8"/><rect x="21" y="25" width="8" height="8"/><rect x="31" y="25" width="8" height="8"/><rect x="11" y="36" width="8" height="8"/><rect x="21" y="36" width="8" height="8"/><rect x="31" y="36" width="8" height="8"/></g><circle cx="25" cy="62" r="3" fill="#3176b5"/></svg>
    </span></div>
    <div class="fact-value">84%</div>
    <p class="fact-text">Sed ut perspiciatis unde omnis iste natus error sit voluptatem accusantium doloremque laudantium.</p>
  </div>

  <div class="fact" style="left:450px">
    <div class="fact-badge"><span style="background:var(--sky-mid)">
      <svg width="60" height="70" viewBox="0 0 60 70" aria-hidden="true"><path d="M22 8a6 6 0 0 1 12 0v24l14 4c5 1.5 7 5 6 10l-4 20H22L8 42c-3-4 2-9 6-6l8 6z" fill="#ffffff"/><path d="M14 12a14 14 0 0 1 28 0" fill="none" stroke="#ffffff" stroke-width="3"/></svg>
    </span></div>
    <div class="fact-value">76%</div>
    <p class="fact-text">Sed ut perspiciatis unde omnis iste natus error sit voluptatem accusantium doloremque laudantium.</p>
  </div>

  <div class="fact" style="left:800px">
    <div class="fact-badge"><span style="background:var(--teal)">
      <svg width="64" height="64" viewBox="0 0 64 64" aria-hidden="true"><path d="M30 6h24v24L28 56 4 32z" fill="#ffffff"/><circle cx="45" cy="16" r="4" fill="#33b8a4"/><path d="M45 16 58 4" stroke="#ffffff" stroke-width="3"/></svg>
    </span></div>
    <div class="fact-value">55%</div>
    <p class="fact-text">Sed ut perspiciatis unde omnis iste natus error sit voluptatem accusantium doloremque laudantium.</p>
  </div>
</section>

<section class="pricing">
  <h2 class="section-title" style="top:38px">Our Pricing</h2>
  <div class="placeholder pricing-device" role="img" aria-label="Smartphone lying at an angle showing the demo shop product grid"></div>
  <p class="pricing-lead">Vorbo is a service that can deliver instant apps for quillora shops. So every shop owner can have its own app for selling to there customers.</p>
  <p class="pricing-copy">At vero eos et accusamus et iusto odio dignissimos ducimus qui blanditiis praesentium voluptatum deleniti atque corrupti quos dolores et quas molestias excepturi sint occaecati cupiditate non provident, similique sunt in culpa qui officia deserunt mollitia animi, id est laborum et dolorum fuga. Et harum quidem rerum facilis est et expedita distinctio.</p>
  <a class="btn btn-coral" style="left:100px;top:355px;width:236px;height:50px">VIEW TO OUR PRICING</a>
</section>

<section class="reviews">
  <h2 class="section-title" style="top:40px;font-size:36px;color:var(--white)">Customer Reviews</h2>
  <svg class="slider-arrow" style="left:96px;top:150px" viewBox="0 0 22 40" aria-hidden="true"><polyline points="16,8 6,20 16,32" fill="none" stroke="#ffffff" stroke-opacity=".6" stroke-width="3"/></svg>
  <svg class="slider-arrow" style="right:96px;top:150px" viewBox="0 0 22 40" aria-hidden="true"><polyline points="6,8 16,20 6,32" fill="none" stroke="#ffffff" stroke-opacity=".6" stroke-width="3"/></svg>
  <p class="review-quote">“ Pellentesque convallis molestie enim sit amet efficitur amet consequat risus.</p>
  <p class="review-body">Nullam accumsan purus vel tempus viverra. Mauris suscipit felis id nunc elementum varius. Praesent elementum nulla sit amet justo pellentesque scelerisque. Nam et tortor in ante iaculis porttitor in luctus mi. Vivamus gravida sem a pretium euismod. ”</p>
  <div class="review-author">
    <div class="avatar" role="img" aria-label="Portrait photo of the reviewer"></div>
    <div>
      <div class="author-name">Tomas Brell, City</div>
      <svg width="110" height="20" viewBox="0 0 110 20" aria-label="Five star rating">
        <g fill="#f5b623">
          <polygon points="10,1 12.6,7 19,7.4 14,11.6 15.6,18 10,14.4 4.4,18 6,11.6 1,7.4 7.4,7"/>
          <polygon transform="translate(22 0)" points="10,1 12.6,7 19,7.4 14,11.6 15.6,18 10,14.4 4.4,18 6,11.6 1,7.4 7.4,7"/>
          <polygon transform="translate(44 0)" points="10,1 12.6,7 19,7.4 14,11.6 15.6,18 10,14.4 4.4,18 6,11.6 1,7.4 7.4,7"/>
          <polygon transform="translate(66 0)" points="10,1 12.6,7 19,7.4 14,11.6 15.6,18 10,14.4 4.4,18 6,11.6 1,7.4 7.4,7"/>
          <polygon transform="translate(88 0)" points="10,1 12.6,7 19,7.4 14,11.6 15.6,18 10,14.4 4.4,18 6,11.6 1,7.4 7.4,7"/>
        </g>
      </svg>
    </div>
  </div>
</section>

<section class="screens">
  <h2 class="section-title" style="top:42px;font-size:37px">Screens of Our Demo Shop</h2>
  <div class="device" style="left:115px"><i class="speaker"></i><div class="screen" role="img" aria-label="Demo shop checkout screen"></div><i class="home"></i></div>
  <div class="device" style="left:372px"><i class="speaker"></i><div class="screen" role="img" aria-label="Demo shop product list screen"></div><i class="home"></i></div>
  <div class="device" style="left:630px"><i class="speaker"></i><div class="screen" role="img" aria-label="Demo shop category gallery screen"></div><i class="home"></i></div>
  <div class="device" style="left:887px"><i class="speaker"></i><div class="screen" role="img" aria-label="Demo shop product grid screen"></div><i class="home"></i></div>
  <div class="dots"><i class="on"></i><i></i><i></i></div>
</section>

<section class="cta">
  <div class="placeholder" role="img" aria-label="Blurred photo of hands holding a smartphone" style="inset:0;background:linear-gradient(120deg,#2c5c9a 0%,#4a79b4 35%,#8fa6c6 60%,#3d68a3 100%)"></div>
  <div class="placeholder" style="inset:0;background:rgba(18,70,140,.35)"></div>
  <h2 class="cta-title">Deliver instant apps for quillora shops</h2>
  <a class="btn btn-coral" style="left:483px;top:230px;width:235px;height:50px">REQUEST A DEMO</a>
</section>

<section class="functions">
  <h2 class="section-title" style="top:45px;font-size:37px">Functionalities of the App</h2>
  <p class="functions-lead">But I must explain to you how all this mistaken idea of denouncing pleasure and praising pain was born and I will give you a complete account of the system</p>
  <p class="functions-copy" style="top:270px">Sed ut perspiciatis unde omnis iste natus error sit voluptatem accusantium doloremque laudantium, totam rem aperiam, eaque ipsa quae ab illo inventore veritatis et quasi architecto beatae vitae dicta sunt explicabo.</p>
  <p class="functions-copy" style="top:355px">Nemo enim ipsam voluptatem quia voluptas sit aspernatur aut odit aut fugit, sed quia consequuntur magni dolores.</p>
  <div class="placeholder" role="img" aria-label="Desktop monitor, tablet and phone showing the app on every screen size" style="left:655px;top:140px;width:445px;height:300px;background:linear-gradient(160deg,#e7edf3 0%,#9fc9e6 55%,#3a9dd6 100%)"></div>
</section>

<footer class="site-footer">
  <div class="col-title" style="left:100px">USEFULL LINKS</div>
  <ul class="link-list" style="left:100px"><li>Home</li><li>Features</li><li>Our Pricing</li><li>Services</li></ul>
  <ul class="link-list" style="left:280px"><li>Products</li><li>Testimonials</li><li>Contact Us</li><li>My Account</li></ul>
  <div class="col-title" style="left:442px">ABOUT US</div>
  <ul class="link-list" style="left:442px"><li>About Vorbo</li><li>Jobs</li><li>Partners</li><li>Blog</li></ul>
  <div class="col-title" style="left:603px">SUPPORT</div>
  <ul class="link-list" style="left:603px"><li>FAQ</li><li>Support</li><li>Team</li><li>Privacy Policy</li></ul>
  <div class="col-title" style="left:776px">SIGN UP FOR NEWSLETTERS</div>
  <p class="newsletter-note">Please sign up here for latest news</p>
  <div class="email-field">EMAIL ADDRESS</div>
  <div class="subscribe">SUBSCRIBE</div>
  <div class="social" aria-label="Social media links"><i></i><i></i><i></i><i></i></div>
  <div class="footer-rule"></div>
  <p class="copyright">© 2016 Company Name. All right reserved. Term of Use</p>
</footer>

</body>
</html>
```